Harborview Estates Business Card for Apartment Buildings

Create business cards for resident managers who run apartment buildings. The audience is the public who are searching for apartment rentals, and current residents who live at the apartment building. Key design element will be incorporating the company logo, however, the logo cannot dominate. The building name and manager name are more important than the logo. Current business card design leaves little room for copy, so we may need to reduce the size on the current card to allow for more space for copy.

Target Market(s)

Adults 18-65 years of age, who are looking for an apartment rental, plus current residents who live at our apartment buildings.

Industry/Entity Type

Property Management

Contact Information for Business Card

A major design element will be use of the company logo. Important property and manager contact information must be part of the design. The size of the logo will need to be reduced to make room for building and manager contact copy.

Font styles to use
Sans Serif

Colors
3176b5
000000
959595
ffffff

Requirements
Must have
• 1) Incorporate the company logo.
• 2) Use the company colors (dark blue, black/grey, over white).
• 3) FEATURE THE BUILDING NAME
• 4) FEATURE THE MANAGER NAME
• 5) The company name is less important than BUILDING and MANAGER
• 6) Manager contact information
• **SEE ATTACHED CREATIVE BRIEF**
Nice to have
• 1) Back of card logo watermark
• 2) Ability to write notes on back of carfd
Should not have
• Avoid letting the company logo dominate the card, the building name and manager are more important than the company logo.

```html
<!DOCTYPE html>
<html lang="en">
<head>
<meta charset="utf-8">
<title>Harborview Estates Business Card</title>
<link href="https://fonts.googleapis.com/css2?family=Jost:wght@400;500;700&display=swap" rel="stylesheet">
<style>
  :root {
    --brand-blue: #3176b5;
    --ink: #000000;
    --slate: #4a4b4d;
    --slate-dark: #3a3b3d;
    --mid-grey: #959595;
    --paper: #ffffff;
    --stage: #ededee;
  }
  html, body {
    margin: 0;
    width: 1200px;
    height: 1172px;
    overflow: hidden;
    background: var(--stage);
    font-family: "Jost", Arial, sans-serif;
  }
  .card {
    position: absolute;
    left: 160px;
    width: 880px;
    height: 502px;
    background: var(--paper);
    box-shadow: 0 6px 18px rgba(0,0,0,0.25);
  }
  .card--front { top: 60px; }
  .card--back { top: 610px; }
  .card svg { display: block; width: 100%; height: 100%; }
  .brand-name { fill: var(--brand-blue); font-weight: 700; font-size: 28px; letter-spacing: 0.5px; }
  .brand-mark { fill: var(--brand-blue); }
  .manager-name { fill: var(--paper); font-weight: 500; font-size: 19px; }
  .manager-title { fill: var(--paper); font-weight: 400; font-size: 13.5px; }
  .contact-line { fill: var(--paper); font-weight: 400; font-size: 13.5px; }
  .icon { fill: var(--paper); }
  .icon-stroke { fill: none; stroke: var(--paper); stroke-width: 1.2; }
</style>
</head>
<body>

<section class="card card--front" aria-label="Business card front">
  <svg viewBox="0 0 535 305" xmlns="http://www.w3.org/2000/svg">
    <defs>
      <linearGradient id="scene-tone" x1="0" y1="0" x2="1" y2="1">
        <stop offset="0" stop-color="#59595b"/>
        <stop offset="0.6" stop-color="#474749"/>
        <stop offset="1" stop-color="#3c3c3e"/>
      </linearGradient>
    </defs>
    <!-- lower photographic panel -->
    <path role="img" aria-label="Muted grey photo of palm trees along a coastline"
          d="M0,158 C110,210 250,150 380,110 C450,90 505,92 535,98 L535,305 L0,305 Z"
          fill="url(#scene-tone)"/>
    <!-- dark swoosh under white band -->
    <path d="M0,140 C110,195 250,135 380,96 C450,78 505,80 535,86 L535,98 C505,92 450,90 380,110 C250,150 110,210 0,158 Z"
          fill="var(--slate-dark)"/>
    <!-- white sweep -->
    <path d="M0,150 C120,196 250,140 380,104 C450,85 505,86 535,92 L535,100 C505,96 450,98 380,116 C250,156 115,208 0,172 Z"
          fill="var(--paper)"/>
    <!-- blue accent -->
    <path d="M320,108 C400,80 480,78 535,88 L535,93 C480,84 400,86 320,108 Z"
          fill="var(--brand-blue)"/>

    <!-- company name -->
    <rect class="brand-mark" x="30" y="34" width="22" height="22"/>
    <text class="brand-name" x="60" y="55">HARBORVIEW ESTATES</text>

    <!-- manager -->
    <text class="manager-name" x="38" y="240">Daniel Whitford</text>
    <text class="manager-title" x="38" y="256">Property Manager</text>

    <!-- contact icons -->
    <rect class="icon-stroke" x="252" y="168" width="6" height="10" rx="1"/>
    <rect class="icon" x="251" y="188" width="9" height="7"/>
    <rect class="icon" x="251" y="207" width="9" height="6"/>
    <circle class="icon-stroke" cx="255.5" cy="228.5" r="4.5"/>
    <line class="icon-stroke" x1="251" y1="228.5" x2="260" y2="228.5"/>
    <path class="icon" d="M255.5,241 a3.5,3.5 0 0 1 3.5,3.5 c0,2.5 -3.5,6 -3.5,6 c0,0 -3.5,-3.5 -3.5,-6 a3.5,3.5 0 0 1 3.5,-3.5 Z"/>

    <!-- contact lines -->
    <text class="contact-line" x="270" y="178">555-318-2046</text>
    <text class="contact-line" x="270" y="197">555-318-7791</text>
    <text class="contact-line" x="270" y="216">info@harborviewest.com</text>
    <text class="contact-line" x="270" y="235">www.harborviewestates.us</text>
    <text class="contact-line" x="270" y="254">2750 Larkspur Ridge Road #B210</text>
    <text class="contact-line" x="270" y="271">Bayfield, CA 90210</text>
  </svg>
</section>

<section class="card card--back" aria-label="Business card back">
  <svg viewBox="0 0 535 305" xmlns="http://www.w3.org/2000/svg">
    <defs>
      <linearGradient id="scene-tone-back" x1="0" y1="0" x2="1" y2="1">
        <stop offset="0" stop-color="#5a5a5c"/>
        <stop offset="1" stop-color="#404042"/>
      </linearGradient>
    </defs>
    <path role="img" aria-label="Muted grey photo of palm trees against the sky"
          d="M0,0 L535,0 L535,125 C470,118 400,105 330,80 C230,40 110,40 0,95 Z"
          fill="url(#scene-tone-back)"/>
    <!-- dark swoosh -->
    <path d="M0,95 C110,40 230,40 330,80 C400,105 470,118 535,125 L535,132 C470,128 400,118 330,96 C230,62 110,60 0,108 Z"
          fill="var(--slate-dark)"/>
    <!-- blue accent -->
    <path d="M330,108 C400,128 470,134 535,132 L535,137 C470,140 400,134 330,108 Z"
          fill="var(--brand-blue)"/>
    <!-- company name -->
    <rect class="brand-mark" x="100" y="186" width="24" height="24"/>
    <text class="brand-name" x="134" y="209">HARBORVIEW ESTATES</text>
  </svg>
</section>

</body>
</html>
```